Marine Services Letterhead design

We need a letterhead design for an Australian owned company in Victoria named K+T Harbour Works Pty Ltd. We provide linesmen and launches to assist the large ships that come into port.
Our colour is orange.
The final design should have a strong nautical theme and communicate safety and reliability.
I would like to use the letter head on invoices so it should print to pdf well.

Target Market(s)

Owners and representatives of shipping companies. It is not for general public

Industry/Entity Type

Nautical

Requirements
Must have
• A shipping theme, not overly complicated, featuring safety orange colours but not all orange of course.
The letterhead should just sit at the top of the page so I can use for invoices.
Nice to have
• Something elegant and stylish
Should not have
• cartoons or pop art

```html
<!DOCTYPE html>
<html lang="en">
<head>
<meta charset="utf-8">
<title>K+T Harbour Works Pty Ltd – Letterhead</title>
<link rel="stylesheet" href="https://fonts.googleapis.com/css2?family=Bodoni+Moda:wght@500&family=Raleway:wght@400&display=swap">
<style>
  :root {
    --frame-yellow: #f9c505;
    --paper: #ffffff;
    --ink: #2b2b2b;
    --ink-soft: #444444;
    --mark-sand: #e8a85a;
  }
  html, body {
    margin: 0;
    padding: 0;
    overflow: hidden;
    background: var(--paper);
  }
  .letterhead {
    position: relative;
    width: 849px;
    height: 1200px;
    box-sizing: border-box;
    border: 20px solid var(--frame-yellow);
    background: var(--paper);
    overflow: hidden;
  }
  .company-name {
    position: absolute;
    left: 32px;
    top: 20px;
    margin: 0;
    font-family: "Bodoni Moda", "Times New Roman", serif;
    font-weight: 500;
    font-size: 20px;
    letter-spacing: 0.3px;
    color: var(--ink);
  }
  .company-details {
    position: absolute;
    left: 32px;
    top: 50px;
    margin: 0;
    font-family: "Raleway", Arial, sans-serif;
    font-size: 14px;
    line-height: 18px;
    color: var(--ink-soft);
    font-style: normal;
  }
  .brand-mark {
    position: absolute;
    left: 648px;
    top: 24px;
    width: 129px;
    height: 88px;
    display: flex;
    flex-direction: column;
    align-items: center;
    justify-content: center;
    gap: 6px;
  }
  .brand-mark__dot {
    width: 26px;
    height: 26px;
    border-radius: 50%;
    background: var(--mark-sand);
  }
  .brand-mark__name {
    font-family: "Raleway", Arial, sans-serif;
    font-size: 13px;
    color: var(--ink);
    text-align: center;
    line-height: 16px;
  }
</style>
</head>
<body>
  <div class="letterhead">
    <h1 class="company-name">K+T Harbour Works Pty Ltd</h1>
    <address class="company-details">
      PO Box 417 Kestrel Point 3931<br>
      Phone: 1300 648 271<br>
      ABN: 72104385619
    </address>
    <div class="brand-mark">
      <span class="brand-mark__dot"></span>
      <span class="brand-mark__name">K+T Harbour Works</span>
    </div>
  </div>
</body>
</html>
```